Retail Sign for Houseplant Campaign

Sign will measure 3 to 4 foot tall by 22.2inches and place on rolling racks of houseplants for a retail promotion in The Birchwell Yard. The theme of the promotion will be "New Year, New You!" Selling points which should be on the sign are Houseplants give you a taste of nature, Houseplants boost air quality inside your home, Indoor plants reduce anxiety, Indoor plants make you more productive, Houseplants improve your concentration and memory.
Updates

Target Market(s)

People who love plants

Industry/Entity Type

Horticulture/ retail

Colors
00AB8E
00BBA5
67D7C9
C6EFE9
E9F9F6
59FF00
82FF00
B8FF75
E3FFCB
F4FFEA
FFF300
FFF600
FEFA6F
FFFEC7
FFFEE8

Requirements
Must have
• Must feel energetic and encourage people to buy plants. Should include 1-2 photos and the selling points listed

```html
<!DOCTYPE html>
<html lang="en">
<head>
<meta charset="UTF-8">
<title>New Year, New You! – Houseplant Sign</title>
<link rel="stylesheet" href="https://fonts.googleapis.com/css2?family=DM+Serif+Display&family=Kumbh+Sans:wght@600&display=swap">
<style>
  :root {
    --teal-bg: #74c6be;
    --cream: #fdfcf0;
    --green: #14ae8e;
    --photo-top: #f1f3ef;
    --photo-mid: #e4ebe1;
    --photo-bottom: #cfdcca;
  }
  html, body {
    margin: 0;
    padding: 0;
    overflow: hidden;
  }
  body {
    width: 726px;
    height: 1200px;
  }
  .sign {
    position: relative;
    width: 726px;
    height: 1200px;
    background: var(--teal-bg);
    overflow: hidden;
  }
  .title-panel {
    position: absolute;
    left: 0;
    top: 176px;
    width: 549px;
    height: 212px;
    background: var(--cream);
    border-bottom-right-radius: 52px;
  }
  .title-panel-tail {
    position: absolute;
    left: 0;
    top: 360px;
    width: 40px;
    height: 28px;
    background: var(--cream);
  }
  .headline {
    position: absolute;
    left: 0;
    top: 0;
    margin: 0;
    font-family: "DM Serif Display", serif;
    font-weight: 400;
    color: var(--green);
    font-size: 78px;
    line-height: 1;
    letter-spacing: -1px;
  }
  .headline span {
    position: absolute;
    white-space: nowrap;
  }
  .headline .line-one { left: 121px; top: 196px; }
  .headline .line-two { left: 213px; top: 264px; }
  .hero-photo {
    position: absolute;
    left: 20px;
    top: 361px;
    width: 672px;
    height: 489px;
    border-top-left-radius: 32px;
    border-bottom-right-radius: 32px;
    background: linear-gradient(160deg, var(--photo-top) 0%, var(--photo-mid) 60%, var(--photo-bottom) 100%);
  }
  .benefits-panel {
    position: absolute;
    left: 226px;
    top: 850px;
    width: 438px;
    height: 255px;
    background: var(--cream);
    border-bottom-left-radius: 36px;
  }
  .benefits {
    list-style: none;
    margin: 0;
    padding: 0;
    font-family: "Kumbh Sans", sans-serif;
    font-weight: 600;
    font-size: 13.8px;
    color: var(--green);
  }
  .benefits li {
    position: absolute;
    left: 31px;
    display: flex;
    align-items: center;
    white-space: nowrap;
  }
  .benefits li:nth-child(1) { top: 50px; }
  .benefits li:nth-child(2) { top: 88px; }
  .benefits li:nth-child(3) { top: 127px; }
  .benefits li:nth-child(4) { top: 167px; }
  .benefits li:nth-child(5) { top: 205px; }
  .leaf-icon {
    width: 15px;
    height: 11px;
    margin-right: 14px;
    flex: none;
  }
</style>
</head>
<body>
  <main class="sign">
    <div class="title-panel"></div>
    <div class="title-panel-tail"></div>
    <h1 class="headline">
      <span class="line-one">New Year,</span>
      <span class="line-two">New You!</span>
    </h1>

    <div class="hero-photo" role="img" aria-label="Photo of a woman relaxing on the floor of a bright living room filled with potted houseplants"></div>

    <section class="benefits-panel">
      <ul class="benefits">
        <li><svg class="leaf-icon" viewBox="0 0 15 11" aria-hidden="true"><path d="M3 11 C0 11 0 7 2 4 C4 1 8 0 15 0 C13 6 10 11 3 11 Z" fill="#14ae8e"/></svg>Houseplants give you a taste of nature</li>
        <li><svg class="leaf-icon" viewBox="0 0 15 11" aria-hidden="true"><path d="M3 11 C0 11 0 7 2 4 C4 1 8 0 15 0 C13 6 10 11 3 11 Z" fill="#14ae8e"/></svg>Houseplants boost air quality inside your home</li>
        <li><svg class="leaf-icon" viewBox="0 0 15 11" aria-hidden="true"><path d="M3 11 C0 11 0 7 2 4 C4 1 8 0 15 0 C13 6 10 11 3 11 Z" fill="#14ae8e"/></svg>Indoor plants reduce anxiety</li>
        <li><svg class="leaf-icon" viewBox="0 0 15 11" aria-hidden="true"><path d="M3 11 C0 11 0 7 2 4 C4 1 8 0 15 0 C13 6 10 11 3 11 Z" fill="#14ae8e"/></svg>Indoor plants make you more productive</li>
        <li><svg class="leaf-icon" viewBox="0 0 15 11" aria-hidden="true"><path d="M3 11 C0 11 0 7 2 4 C4 1 8 0 15 0 C13 6 10 11 3 11 Z" fill="#14ae8e"/></svg>Houseplants improve your concentration and memory.</li>
      </ul>
    </section>
  </main>
</body>
</html>
```